Business Card Design

This is a new cafe in Wavell Heights.
My mantra / (updated) slogan is 'Nourishing Food. Coffee as its Best'
95% of food is produced from my own kitchen.
Breakfast and lunch items on the menu include lots of good stuff on sourdough, all natural smoothies, gluten/dairy free foods/treats as well as more traditional fare. Focus is on wholesome healthy food and fantastic coffee.
Colours are predominantly green from attached logo and black but happy for some coffee bean brown for effect.
Preferred font would be Dilennial UPC per attached logo / flyer.
We have a Facebook page and Instagram account.

Industry/Entity Type

Business

Contact Information for Business Card

Meredith Tallis
Lumen Cafe
384 Pelling Street
Marden Vale QLD 4208

```html
<!DOCTYPE html>
<html lang="en">
<head>
<meta charset="utf-8">
<title>Lumen Cafe Business Card</title>
<link rel="stylesheet" href="https://fonts.googleapis.com/css2?family=Arvo:wght@700&family=Lora:wght@400&family=Open+Sans:wght@400;600;700&display=swap">
<style>
  :root {
    --green: #22b35e;
    --ink: #1c1c1c;
    --grey: #6a6a6a;
    --rule: #3a3a3a;
    --card: #ffffff;
    --card-edge: #ececec;
    --backdrop: #e8e5df;
    --photo-a: #b9a48c;
    --photo-b: #6e5a48;
  }
  * { box-sizing: border-box; margin: 0; padding: 0; }
  html, body {
    width: 1200px; height: 885px; overflow: hidden;
    background: var(--backdrop);
    font-family: "Open Sans", Arial, sans-serif;
    color: var(--ink);
  }
  .stage { position: relative; width: 1200px; height: 885px; }
  .card {
    position: absolute; left: 280px;
    width: 640px; height: 390px;
    background: linear-gradient(160deg, var(--card) 60%, var(--card-edge));
    border-radius: 16px;
    box-shadow: 0 3px 0 #d6d6d6, 0 6px 0 #cfcfcf, 0 14px 28px rgba(0,0,0,.18);
  }
  .card--front { top: 32px; }
  .card--back { top: 462px; }

  .wordmark {
    font-family: "Arvo", Georgia, serif;
    font-weight: 700;
    color: var(--green);
    white-space: nowrap;
  }
  .card--front .wordmark {
    position: absolute; left: 40px; top: 58px;
    font-size: 52px; line-height: 1;
  }
  .slogan {
    position: absolute; left: 42px; top: 126px;
    font-family: "Lora", Georgia, serif;
    font-size: 10.5px; letter-spacing: .4px;
    text-transform: uppercase; color: var(--ink);
    white-space: nowrap;
  }
  .divider {
    position: absolute; left: 40px; right: 44px; top: 150px;
    border-top: 1px solid var(--rule);
  }
  .portrait {
    position: absolute; right: 44px; top: 28px;
    width: 132px; height: 80px;
    border: 3px solid #3b3b3b; border-radius: 4px;
    background: linear-gradient(135deg, var(--photo-a), var(--photo-b));
  }
  .person__name {
    position: absolute; right: 44px; top: 114px;
    font-size: 20px; font-weight: 700; color: var(--green);
    line-height: 1.2; white-space: nowrap;
  }
  .person__role {
    position: absolute; right: 44px; top: 154px;
    font-size: 14px; color: var(--grey);
  }
  .menu {
    position: absolute; right: 44px; top: 180px;
    list-style: none; text-align: right;
    font-size: 14px; line-height: 20px;
  }
  .menu li { white-space: nowrap; }
  .menu li::after {
    content: ""; display: inline-block;
    width: 6px; height: 6px; border-radius: 50%;
    background: var(--green); margin-left: 10px; vertical-align: middle;
  }
  .contact {
    position: absolute; left: 44px; top: 296px;
    font-size: 15px; line-height: 26px;
  }
  .contact__row { display: flex; align-items: center; gap: 10px; }
  .contact__icon {
    width: 18px; height: 18px; border-radius: 3px;
    background: var(--green); display: inline-flex;
    align-items: center; justify-content: center;
  }
  .card--back .wordmark {
    position: absolute; left: 0; right: 0; top: 150px;
    text-align: center; font-size: 76px; line-height: 1;
  }
</style>
</head>
<body>
<main class="stage">
  <section class="card card--front" aria-label="Business card front">
    <div class="wordmark">Lumen Cafe</div>
    <p class="slogan">Wholesome food made by hand. Coffee done right</p>
    <div class="divider"></div>

    <div class="portrait" role="img" aria-label="Portrait photo of the owner"></div>
    <p class="person__name">Meredith Tallis</p>
    <p class="person__role">Owner</p>

    <ul class="menu">
      <li>Milkshakes</li>
      <li>Frappes</li>
      <li>All-natural Smoothies</li>
      <li>Home-made burgers</li>
      <li>salads and Gourmet Sandwiches</li>
    </ul>

    <div class="contact">
      <p>384 Pelling Street, Marden Vale QLD 4208</p>
      <p class="contact__row">
        <span class="contact__icon">
          <svg width="12" height="12" viewBox="0 0 24 24" aria-hidden="true">
            <path fill="#fff" d="M6.6 10.8a15.1 15.1 0 0 0 6.6 6.6l2.2-2.2c.3-.3.7-.4 1-.2 1.1.4 2.3.6 3.6.6.6 0 1 .4 1 1V20c0 .6-.4 1-1 1A17 17 0 0 1 3 4c0-.6.4-1 1-1h3.5c.6 0 1 .4 1 1 0 1.3.2 2.5.6 3.6.1.3 0 .7-.2 1z"/>
          </svg>
        </span>
        0491570156
      </p>
      <p class="contact__row"><span class="contact__icon"></span>lumencafe</p>
    </div>
  </section>

  <section class="card card--back" aria-label="Business card back">
    <div class="wordmark">Lumen Cafe</div>
  </section>
</main>
</body>
</html>
```